New Business Card Design Project

Use the flyer uploaded and website www.brightoakbuilders.com for inspiration.
List Our Services on Backside of business cards
Marcus Delling
Harborline Builders Inc.
Licensed General Contractors
858-471-6093

Contact Information for Business Card

Use the flyer uploaded and website www.brightoakbuilders.com for inspiration. List Our Services on Backside of business cards Marcus Delling Harborline Builders Inc. Licensed General Contractors 858-471-6093

```html
<!DOCTYPE html>
<html lang="en">
<head>
<meta charset="UTF-8">
<title>Harborline Builders – Business Card</title>
<link href="https://fonts.googleapis.com/css2?family=Tinos:wght@400;700&display=swap" rel="stylesheet">
<style>
  :root {
    --page-bg: #e9e6e1;
    --card-bg: #0b0b0b;
    --ink: #f2f2f2;
    --ink-soft: #cfcfcf;
    --rule: rgba(255,255,255,0.35);
    --shadow: rgba(0,0,0,0.28);
  }
  * { box-sizing: border-box; margin: 0; padding: 0; }
  html, body {
    width: 1200px; height: 900px; overflow: hidden;
    background: var(--page-bg);
    font-family: "Tinos", "Times New Roman", serif;
  }
  .sheet {
    width: 1200px; height: 900px;
    display: flex; flex-direction: column;
    align-items: center; justify-content: center; gap: 56px;
  }
  .card {
    width: 580px; height: 331px;
    background: var(--card-bg);
    border-radius: 30px;
    box-shadow: 0 14px 30px var(--shadow);
    color: var(--ink);
    display: flex; flex-direction: column; align-items: center;
    text-align: center;
  }
  .brand-name {
    display: flex; align-items: center; gap: 10px;
    font-size: 24px; font-weight: 400; letter-spacing: 2px;
    text-transform: uppercase; color: var(--ink);
  }
  .brand-dot {
    width: 10px; height: 10px; border-radius: 50%;
    border: 1px solid var(--ink);
  }
  .rule {
    width: 62%; height: 1px;
    background: linear-gradient(90deg, transparent, var(--rule), transparent);
  }

  /* Services side */
  .card--services { padding-top: 40px; }
  .card--services .brand-name { margin-bottom: 18px; }
  .services-title {
    font-weight: 700; font-size: 20px; letter-spacing: 0.5px;
    margin-bottom: 10px;
  }
  .services-list { list-style: none; font-size: 16px; line-height: 1.3; color: var(--ink-soft); }
  .card--services .rule { margin: 14px 0 10px; }
  .guarantee { font-weight: 700; font-size: 18px; }

  /* Contact side */
  .card--contact { padding-top: 52px; }
  .card--contact .brand-name { font-size: 28px; margin-bottom: 22px; }
  .card--contact .rule { margin: 0 0 14px; }
  .person-name { font-weight: 700; font-size: 22px; letter-spacing: 1px; text-transform: uppercase; }
  .person-role { font-size: 17px; color: var(--ink-soft); margin: 4px 0 14px; }
  .call-to-action { font-weight: 700; font-size: 21px; margin: 4px 0 6px; }
  .contact-line {
    display: flex; align-items: center; gap: 8px;
    font-size: 17px; color: var(--ink);
  }
  .contact-line svg { width: 16px; height: 16px; }
  .divider { opacity: 0.8; }
</style>
</head>
<body>
<main class="sheet">

  <section class="card card--services" aria-label="Business card services side">
    <div class="brand-name"><span class="brand-dot"></span>Harborline Builders</div>
    <h2 class="services-title">OUR SERVICES</h2>
    <ul class="services-list">
      <li>Remodel - Kitchen &amp; Bath / Painting - Interior &amp; Exterior</li>
      <li>Flooring - Carpet, Vinyl, Wood / Window &amp; Door Replacement</li>
      <li>Plumbing - Repairs &amp; Upgrades / Energy - Efficient Upgrades</li>
      <li>Deck &amp; Patio Construction / Water &amp; Mold Damage / Garage Renovation</li>
    </ul>
    <div class="rule"></div>
    <p class="guarantee">Our Services Are 100% Guaranteed</p>
  </section>

  <section class="card card--contact" aria-label="Business card contact side">
    <div class="brand-name"><span class="brand-dot"></span>Harborline Builders</div>
    <div class="rule"></div>
    <h1 class="person-name">Marcus Delling</h1>
    <p class="person-role">Harborline Builders Inc. - Licensed General Contractors</p>
    <div class="rule"></div>
    <p class="call-to-action">Call/Text Or Book Online</p>
    <p class="contact-line">
      <svg viewBox="0 0 24 24" aria-hidden="true"><path fill="currentColor" d="M6.6 10.8a15 15 0 0 0 6.6 6.6l2.2-2.2a1 1 0 0 1 1-.25 11.4 11.4 0 0 0 3.6.57 1 1 0 0 1 1 1V20a1 1 0 0 1-1 1A17 17 0 0 1 3 4a1 1 0 0 1 1-1h3.5a1 1 0 0 1 1 1c0 1.25.2 2.45.57 3.57a1 1 0 0 1-.25 1z"/></svg>
      <span>858-471-6093</span>
      <span class="divider">|</span>
      <svg viewBox="0 0 24 24" aria-hidden="true" fill="none" stroke="currentColor" stroke-width="1.6"><circle cx="12" cy="12" r="9"/><ellipse cx="12" cy="12" rx="4" ry="9"/><path d="M3 12h18M5 7h14M5 17h14"/></svg>
      <span>www.brightoakbuilders.com</span>
    </p>
  </section>

</main>
</body>
</html>
```